Kelvaro.ch is looking for business card letterhead and envelope C5 with WOW effect

We need a strong business card for our company Kelvaro.ch, logo is available. You want a black or dark background on which the logo Stark r% 26 # 252; appears. Letterhead and envelope in C5 format should be in a similar design, but does not have to be We need a strong business card for our company Kelvaro.ch, logo is available. A black or dark background is desired, on which the logo Stark comes across. The letterhead and the envelope in C5 format should have a similar design.

Target Market(s)

Private customers as well as entrepreneurs

Contact Information for Business Card

E-mail: info@kelvaro-example.ch
Web.www.Kelvaro-example.ch
Tel: +41 ( 0 ) 79 482 6037
Adresse:
Lindenweg 14
9406 Tarnbach

Hier kann man Icons verwenden für Email,Tel und Adressse

Font styles to use
Other font styles liked:
• Dubai,bold

Colors

Designer to choose colors to be used in the design.

Requirements
Must have
• WOW effect
Nice to have
• R% 26 # 252; back business card with our service listings. - VEHICLE LABELING - SHOP WINDOW LABELING - STICKERS AND MUCH MORE ... in red color

```html
<!DOCTYPE html>
<html lang="en">
<head>
<meta charset="utf-8">
<title>Kelvaro.ch – Business Card</title>
<link rel="stylesheet" href="https://fonts.googleapis.com/css2?family=Ubuntu:wght@400;500;700&display=swap">
<style>
  :root {
    --stage: #3a3530;
    --navy: #14203f;
    --navy-deep: #0f1933;
    --navy-light: #1d2c52;
    --white: #ffffff;
    --yellow: #f5c92a;
    --red: #e0252b;
    --muted: #dfe4ef;
  }
  * { box-sizing: border-box; margin: 0; padding: 0; }
  html, body {
    width: 1200px; height: 930px; overflow: hidden;
    background: var(--stage);
    font-family: "Ubuntu", sans-serif;
  }
  .canvas { position: relative; width: 1200px; height: 930px; }

  .card {
    position: absolute;
    width: 560px; height: 320px;
    border-radius: 22px;
    background: linear-gradient(120deg, var(--navy-light) 0%, var(--navy) 45%, var(--navy-deep) 100%);
    color: var(--white);
    overflow: hidden;
  }
  .card--front { left: 70px; top: 110px; }
  .card--back  { left: 570px; top: 500px; }

  /* front */
  .brand {
    display: flex; align-items: center; gap: 14px;
    font-weight: 700; letter-spacing: 1px;
    text-transform: uppercase;
  }
  .brand__square { width: 18px; height: 18px; background: var(--yellow); }
  .card--front .brand { position: absolute; left: 150px; top: 100px; font-size: 40px; }

  .services {
    position: absolute; right: 58px; top: 170px;
    list-style: none; text-align: right;
    font-size: 14px; line-height: 20px; text-transform: uppercase;
    color: var(--muted);
  }
  .services li { display: flex; align-items: center; justify-content: flex-end; gap: 8px; }
  .services li::after {
    content: ""; width: 7px; height: 7px; border-radius: 50%;
    border: 2px solid var(--red);
  }

  /* back */
  .card--back .brand {
    position: absolute; left: 0; right: 0; top: 44px;
    justify-content: center; font-size: 28px;
  }
  .person {
    position: absolute; right: 312px; top: 152px; text-align: right;
  }
  .person__name { font-size: 26px; font-weight: 700; text-transform: uppercase; letter-spacing: .5px; }
  .person__surname { color: var(--yellow); }
  .person__role { font-size: 15px; margin-top: 4px; color: var(--muted); }

  .divider {
    position: absolute; left: 272px; top: 132px;
    width: 1px; height: 92px; background: var(--yellow);
  }
  .contacts {
    position: absolute; left: 296px; top: 136px;
    list-style: none; font-size: 15px; line-height: 27px;
  }
  .contacts li { display: flex; align-items: center; gap: 10px; }
  .contacts svg { width: 13px; height: 13px; flex: none; }
  .address {
    position: absolute; left: 0; right: 0; bottom: 40px;
    text-align: center; font-size: 16px; letter-spacing: .3px;
  }
</style>
</head>
<body>
<main class="canvas">

  <section class="card card--front" aria-label="Business card front">
    <div class="brand"><span class="brand__square"></span><span>Kelvaro.ch</span></div>
    <ul class="services">
      <li>Vehicle labeling</li>
      <li>Shop window labeling</li>
      <li>Stickers and much more</li>
    </ul>
  </section>

  <section class="card card--back" aria-label="Business card back">
    <div class="brand"><span>Kelvaro.ch</span></div>

    <div class="person">
      <p class="person__name">Lukas <span class="person__surname">Brenner</span></p>
      <p class="person__role">Director</p>
    </div>

    <div class="divider"></div>

    <ul class="contacts">
      <li>
        <svg viewBox="0 0 24 24" aria-hidden="true"><path fill="#f5c92a" d="M6.6 10.8a15.1 15.1 0 0 0 6.6 6.6l2.2-2.2a1 1 0 0 1 1-.25 11.4 11.4 0 0 0 3.6.57 1 1 0 0 1 1 1V20a1 1 0 0 1-1 1A17 17 0 0 1 3 4a1 1 0 0 1 1-1h3.5a1 1 0 0 1 1 1c0 1.25.2 2.45.57 3.57a1 1 0 0 1-.25 1z"/></svg>
        +41 ( 0 ) 79 482 6037
      </li>
      <li>
        <svg viewBox="0 0 24 24" aria-hidden="true"><rect x="2.5" y="5" width="19" height="14" rx="1.5" fill="none" stroke="#f5c92a" stroke-width="2.4"/><path d="M3 6l9 7 9-7" fill="none" stroke="#f5c92a" stroke-width="2.4"/></svg>
        info@kelvaro-example.ch
      </li>
      <li>
        <svg viewBox="0 0 24 24" aria-hidden="true"><circle cx="12" cy="12" r="9.5" fill="none" stroke="#f5c92a" stroke-width="2.2"/><path d="M2.5 12h19M12 2.5c3 3 3 16 0 19M12 2.5c-3 3-3 16 0 19" fill="none" stroke="#f5c92a" stroke-width="1.8"/></svg>
        www.kelvaro-example.ch
      </li>
    </ul>

    <p class="address">Lindenweg 14 9406 Tarnbach</p>
  </section>

</main>
</body>
</html>
```